business card Calvanto

Wee need a business card design for a new compagny based on Paris
We developped innovative a platform for selling services to refresh, beautify and develop its housing.
We would like a red logo on a black background
Te final design should communicate quality service, know-how, high-end

Target Market(s)

individuals

Industry/Entity Type

Business

```html
<!DOCTYPE html>
<html lang="en">
<head>
<meta charset="utf-8">
<title>Calvanto business card</title>
<link href="https://fonts.googleapis.com/css2?family=Didact+Gothic&family=Open+Sans:wght@400;700&display=swap" rel="stylesheet">
<style>
  :root {
    --backdrop: #e4e4e4;
    --card-dark: #0c0c0c;
    --card-mid: #1c1c1c;
    --coral: #e5625f;
    --wordmark: #b9b9b9;
    --text-light: #f2f2f2;
    --panel: #ffffff;
  }
  * { box-sizing: border-box; margin: 0; padding: 0; }
  html, body { width: 1200px; height: 852px; overflow: hidden; }
  body {
    background: radial-gradient(ellipse at center, #f1f1f1 0%, var(--backdrop) 75%);
    font-family: "Open Sans", Arial, sans-serif;
    position: relative;
  }
  .card {
    position: absolute;
    width: 520px;
    height: 300px;
    border-radius: 26px;
    overflow: hidden;
    background: linear-gradient(135deg, var(--card-mid) 0%, var(--card-dark) 55%, #000 100%);
    box-shadow: 0 10px 24px rgba(0,0,0,0.28);
  }
  .card--front { left: 60px; top: 140px; }
  .card--back { left: 620px; top: 410px; }

  .brand { display: flex; align-items: center; gap: 14px; }
  .brand__mark { background: var(--coral); flex: none; }
  .brand__name {
    font-family: "Didact Gothic", Arial, sans-serif;
    color: var(--wordmark);
    line-height: 1;
  }
  .card--front .brand {
    position: absolute; left: 0; right: 0; top: 50%;
    transform: translateY(-50%); justify-content: center;
  }
  .card--front .brand__mark { width: 62px; height: 62px; }
  .card--front .brand__name { font-size: 60px; }

  .card--back .brand { position: absolute; left: 30px; top: 48px; }
  .card--back .brand__mark { width: 44px; height: 44px; }
  .card--back .brand__name { font-size: 42px; }

  .contact { position: absolute; left: 30px; top: 130px; }
  .contact__name { color: var(--coral); font-weight: 700; font-size: 16px; }
  .contact__role { color: var(--text-light); font-size: 10px; margin-bottom: 14px; }
  .contact__list { list-style: none; color: var(--text-light); font-size: 11.5px; line-height: 17px; }
  .contact__list li { display: flex; align-items: center; gap: 9px; }
  .contact__list svg { width: 11px; height: 11px; fill: var(--coral); flex: none; }
  .contact__site span { color: var(--coral); }
  .contact__address { color: var(--text-light); font-size: 11.5px; line-height: 16px; margin-top: 6px; padding-left: 20px; }

  .feature-panel {
    position: absolute; right: -30px; top: 40px;
    width: 230px; height: 230px;
    background: var(--panel);
    border-radius: 28px;
    border: 14px solid var(--coral);
    box-shadow: 0 0 0 8px var(--panel);
  }
</style>
</head>
<body>
  <section class="card card--front">
    <div class="brand">
      <span class="brand__mark"></span>
      <span class="brand__name">Calvanto</span>
    </div>
  </section>

  <section class="card card--back">
    <div class="brand">
      <span class="brand__mark"></span>
      <span class="brand__name">Calvanto</span>
    </div>

    <div class="contact">
      <p class="contact__name">Your Long Name</p>
      <p class="contact__role">Managing Director</p>
      <ul class="contact__list">
        <li><svg viewBox="0 0 12 12"><path d="M2 1h3l1 3-1.5 1a6 6 0 0 0 2.5 2.5L8 6l3 1v3a1 1 0 0 1-1 1A9 9 0 0 1 1 2a1 1 0 0 1 1-1z"/></svg>00.00.00.0000</li>
        <li><svg viewBox="0 0 12 12"><path d="M3 0h6a1 1 0 0 1 1 1v10a1 1 0 0 1-1 1H3a1 1 0 0 1-1-1V1a1 1 0 0 1 1-1zm0 2v7h6V2z"/></svg>00.00.00.0000</li>
        <li><svg viewBox="0 0 12 12"><path d="M0 2h12v8H0zm1 1v.4l5 3.2 5-3.2V3z"/></svg>yourname@yourwebsite.com</li>
        <li class="contact__site"><svg viewBox="0 0 12 12"><circle cx="6" cy="6" r="5.5"/></svg>www.<span>yourwebsite</span>.com</li>
      </ul>
      <p class="contact__address">Your Commercial or office address<br>in just two line with pincode</p>
    </div>

    <div class="feature-panel" role="img" aria-label="Large brand symbol decoration"></div>
  </section>
</body>
</html>
```